Specialised investor in e-mobility and energy wants business card design

We need a business card design that fits our existing corporate design. <The look and feel must be 'sharp'/'clean', dynamic, communicate momentum, professionalism etc (as one would imagine from a firm in the financial sector). We like the idea of a reverse-side of the card that includes the logo, and the name and contact details on the other. We expect the deliverable to be whatever format might be required to be able to get cards printed directly by a service such as kelmo press. Our website is www.zub.capital

```html
<!DOCTYPE html>
<html lang="en">
<head>
<meta charset="utf-8">
<title>Zub Capital – Business Card</title>
<link href="https://fonts.googleapis.com/css2?family=Arimo:wght@400;700&family=Questrial&display=swap" rel="stylesheet">
<style>
  :root {
    --page: #141414;
    --card: #272727;
    --card-deep: #202020;
    --pattern: #2e2e2e;
    --white: #f4f4f4;
    --muted: #d8d8d8;
    --green: #6aa332;
  }
  * { box-sizing: border-box; margin: 0; padding: 0; }
  html, body { width: 1200px; height: 963px; overflow: hidden; }
  body {
    background: var(--page);
    display: flex;
    flex-direction: column;
    align-items: center;
    justify-content: center;
    gap: 50px;
    font-family: "Arimo", Arial, sans-serif;
    color: var(--white);
  }
  .card {
    position: relative;
    width: 620px;
    height: 400px;
    border-radius: 28px;
    background: radial-gradient(ellipse at 55% 40%, #2d2d2d 0%, var(--card) 55%, var(--card-deep) 100%);
    border-bottom: 4px solid var(--green);
    overflow: hidden;
  }
  .wordmark {
    display: flex;
    align-items: center;
    gap: 14px;
    font-family: "Questrial", Arial, sans-serif;
    font-weight: 400;
    color: var(--white);
    letter-spacing: 1px;
  }
  .wordmark .dot {
    width: 18px; height: 18px;
    border-radius: 50%;
    background: var(--green);
  }
  /* front */
  .card-front .wordmark {
    position: absolute;
    top: 110px; left: 0; right: 0;
    justify-content: center;
    font-size: 58px;
  }
  .holder {
    position: absolute;
    top: 255px; left: 70px;
    width: 220px;
    text-align: right;
  }
  .holder-name {
    font-weight: 700;
    font-size: 19px;
    letter-spacing: 0.5px;
    text-transform: uppercase;
  }
  .holder-name .surname { color: var(--green); }
  .holder-city { font-size: 17px; color: var(--muted); margin-top: 6px; }
  .divider {
    position: absolute;
    top: 245px; left: 312px;
    width: 1px; height: 90px;
    background: var(--muted);
  }
  .contacts {
    position: absolute;
    top: 248px; left: 332px;
    list-style: none;
    font-size: 17px;
  }
  .contacts li { display: flex; align-items: center; gap: 12px; height: 28px; }
  .contacts svg { width: 18px; height: 18px; fill: var(--green); flex: none; }
  /* back */
  .pattern-field {
    position: absolute; inset: 0;
    background: repeating-linear-gradient(120deg, var(--pattern) 0 40px, var(--card) 40px 80px);
    opacity: 0.6;
  }
  .card-back .wordmark {
    position: absolute;
    top: 160px; left: 0; right: 0;
    justify-content: center;
    font-size: 58px;
  }
</style>
</head>
<body>
  <section class="card card-front" aria-label="Card front">
    <div class="wordmark"><span class="dot"></span><span>Zub Capital</span></div>
    <div class="holder">
      <p class="holder-name">Lena <span class="surname">Varholt</span></p>
      <p class="holder-city">Basel, Switzerland</p>
    </div>
    <div class="divider"></div>
    <ul class="contacts">
      <li>
        <svg viewBox="0 0 24 24"><path d="M6.6 10.8a15 15 0 0 0 6.6 6.6l2.2-2.2c.3-.3.7-.4 1-.2 1.1.4 2.3.6 3.6.6.6 0 1 .4 1 1V20c0 .6-.4 1-1 1A17 17 0 0 1 3 4c0-.6.4-1 1-1h3.5c.6 0 1 .4 1 1 0 1.3.2 2.5.6 3.6.1.3 0 .7-.2 1z"/></svg>
        <span>+41 79555 0148</span>
      </li>
      <li>
        <svg viewBox="0 0 24 24"><path d="M2 5h20v14H2z M2 5l10 8 10-8" fill="none" stroke="#6aa332" stroke-width="2"/></svg>
        <span>lena@zub.capital</span>
      </li>
      <li>
        <svg viewBox="0 0 24 24"><circle cx="12" cy="12" r="10"/></svg>
        <span>www.zub.capital</span>
      </li>
    </ul>
  </section>

  <section class="card card-back" aria-label="Card back">
    <div class="pattern-field" role="img" aria-label="Subtle embossed repeating brand pattern in dark grey"></div>
    <div class="wordmark"><span class="dot"></span><span>Zub Capital</span></div>
  </section>
</body>
</html>
```